Hi Morvina, we need our wine labels produced for this year's vintage with a few changes. We would like to keep the integrity of the current label for the H and want the blue and gold to remain in the design. However we would like to include an image of a tree and our dogs.

```html
<!DOCTYPE html>
<html lang="en">
<head>
<meta charset="utf-8">
<title>Carrowby Estate – Aldric's Paddock Pinot Noir 2019</title>
<link rel="stylesheet" href="https://fonts.googleapis.com/css2?family=Arimo:wght@400;700&family=Archivo:wght@700&family=Parisienne&display=swap">
<style>
  :root {
    --navy: #1f2063;
    --gold: #8a6e2b;
    --gold-text: #7c6325;
    --ink: #111111;
    --paper: #ffffff;
    --backdrop: #eef0f1;
  }
  * { margin: 0; padding: 0; box-sizing: border-box; }
  html, body {
    width: 1200px;
    height: 923px;
    overflow: hidden;
    background: var(--backdrop);
  }
  .canvas {
    position: relative;
    width: 1200px;
    height: 923px;
  }
  .label {
    position: absolute;
    left: 130px;
    top: 31px;
    width: 532px;
    height: 487px;
    background: var(--paper);
    transform: scale(1.766);
    transform-origin: top left;
    font-family: "Arimo", Arial, sans-serif;
    color: var(--ink);
  }
  .label__top-band {
    position: absolute;
    left: 0; top: 0;
    width: 532px;
    height: 80px;
  }
  .label__bottom-band {
    position: absolute;
    left: 0; bottom: 0;
    width: 532px;
    height: 26px;
  }
  .label__mark {
    position: absolute;
    left: 248px;
    top: 44px;
    width: 36px;
    height: 38px;
    background: var(--gold);
  }
  .label__estate {
    position: absolute;
    left: 0; width: 100%;
    top: 88px;
    text-align: center;
    font-family: "Archivo", "Arimo", sans-serif;
    font-weight: 700;
    font-size: 34px;
    line-height: 1;
    letter-spacing: 0.2px;
    color: var(--gold-text);
  }
  .label__range {
    position: absolute;
    left: 0; width: 100%;
    top: 126px;
    text-align: center;
    font-family: "Parisienne", cursive;
    font-size: 33px;
    line-height: 1;
    color: var(--navy);
  }
  .label__artwork {
    position: absolute;
    left: 202px;
    top: 166px;
    width: 132px;
    height: 214px;
  }
  .label__variety {
    position: absolute;
    left: 0; width: 100%;
    top: 389px;
    text-align: center;
    font-weight: 700;
    font-size: 17px;
    line-height: 1;
  }
  .label__vintage {
    position: absolute;
    left: 0; width: 100%;
    top: 410px;
    text-align: center;
    font-weight: 700;
    font-size: 17px;
    line-height: 1;
  }
  .label__region {
    position: absolute;
    left: 0; width: 100%;
    top: 431px;
    text-align: center;
    font-weight: 700;
    font-size: 12.5px;
    line-height: 1;
  }
  .label__additive {
    position: absolute;
    left: 7px;
    top: 446px;
    font-size: 11.5px;
    line-height: 1;
  }
  .label__volume,
  .label__alcohol {
    position: absolute;
    right: 7px;
    font-size: 11.5px;
    line-height: 1;
    text-align: right;
  }
  .label__volume { top: 430px; }
  .label__alcohol { top: 446px; }
</style>
</head>
<body>
<main class="canvas">
  <section class="label">
    <svg class="label__top-band" viewBox="0 0 532 80" role="img" aria-label="Navy and gold chevron pattern band">
      <rect x="0" y="0" width="532" height="66" fill="var(--navy)"/>
      <rect x="0" y="66" width="532" height="14" fill="var(--gold)"/>
      <rect x="0" y="68" width="532" height="4" fill="#ffffff" opacity="0.35"/>
      <path d="M212 80 L212 88 A55 55 0 0 1 322 88 L322 80 Z" fill="var(--paper)"/>
      <path d="M212 82 A55 55 0 0 1 322 82 L322 80 L212 80 Z" fill="var(--paper)"/>
      <circle cx="267" cy="88" r="55" fill="var(--paper)"/>
    </svg>
    <div class="label__mark" aria-hidden="true"></div>
    <h1 class="label__estate">CARROWBY ESTATE</h1>
    <h2 class="label__range">Aldric’s Paddock</h2>
    <svg class="label__artwork" viewBox="0 0 132 214" role="img" aria-label="Illustration of a tall tree with two dogs resting beneath it">
      <defs>
        <linearGradient id="tree-tone" x1="0" y1="0" x2="0" y2="1">
          <stop offset="0" stop-color="#9a7d35"/>
          <stop offset="1" stop-color="#7a6024"/>
        </linearGradient>
      </defs>
      <rect x="0" y="0" width="132" height="214" fill="url(#tree-tone)"/>
    </svg>
    <p class="label__variety">PINOT NOIR</p>
    <p class="label__vintage">2019</p>
    <p class="label__region">MORNINGTON PENINSULA</p>
    <p class="label__additive">Preservative 220 added</p>
    <p class="label__volume">750 ml</p>
    <p class="label__alcohol">ALC/VOL 13%</p>
    <svg class="label__bottom-band" viewBox="0 0 532 26" role="img" aria-label="Gold chevron pattern band">
      <rect x="0" y="0" width="532" height="26" fill="var(--gold)"/>
    </svg>
  </section>
</main>
</body>
</html>
```